HR services to some of biggest Silicon Valley Tech companies needs a new website

We need a new website design probably 4-5 pages initially. Here are some websites we like the look of https://quenmarport.com/ , https://www.vribly.com/ and https://fennix.com/ .

Target Market(s)

Silicon valley tech companies

Industry/Entity Type

HR

Coding

Coded - Design and coding required

Number of Pages Required

5+ page

Requirements
Nice to have
• any stock photos or images should show a diverse group of people. Our client base is very diverse

```html
<!DOCTYPE html>
<html lang="en">
<head>
<meta charset="utf-8">
<title>HR Vantor Consulting</title>
<link href="https://fonts.googleapis.com/css2?family=Exo+2:wght@500;600;700&family=Arimo:wght@400;700&display=swap" rel="stylesheet">
<style>
:root{
  --yellow:#fbb90f;
  --dark:#3d3d3d;
  --footer:#333333;
  --ink:#2f2f2f;
  --grey:#6b6b6b;
  --white:#ffffff;
  --line:#e4e4e4;
}
*{box-sizing:border-box;margin:0;padding:0}
html,body{width:1200px;height:4204px;overflow:hidden}
body{position:relative;background:var(--white);font-family:"Arimo",Arial,sans-serif;color:var(--ink)}
.abs{position:absolute}
.display{font-family:"Exo 2",sans-serif;text-transform:uppercase;letter-spacing:.5px}
.btn{position:absolute;display:flex;align-items:center;justify-content:center;background:var(--yellow);color:var(--white);border-radius:30px;font-family:"Exo 2",sans-serif;font-weight:600;text-transform:uppercase;font-size:16px;letter-spacing:.5px}

/* header */
.site-header{position:absolute;left:0;top:0;width:1200px;height:180px;background:var(--white)}
.brand{position:absolute;left:110px;top:100px;display:flex;align-items:center;gap:12px}
.brand-dot{width:22px;height:22px;background:var(--yellow)}
.brand-name{font-family:"Exo 2",sans-serif;font-weight:600;font-size:26px;color:var(--dark);text-transform:uppercase;line-height:1}
.main-nav{position:absolute;left:372px;top:126px;display:flex;gap:34px;font-family:"Exo 2",sans-serif;font-weight:600;font-size:15px;text-transform:uppercase;color:var(--dark)}
.main-nav .active{color:var(--yellow)}

/* hero */
.hero{position:absolute;left:0;top:180px;width:1200px;height:698px;background:linear-gradient(100deg,#3b3f45 0%,#23272c 45%,#14171a 100%)}
.hero h1{position:absolute;left:110px;top:262px;font-family:"Exo 2",sans-serif;font-weight:700;font-size:54px;line-height:66px;color:var(--white);text-transform:uppercase}
.hero h1 span{display:block;color:var(--yellow);font-size:68px}
.hero p{position:absolute;left:110px;top:412px;font-family:"Exo 2",sans-serif;font-weight:600;font-size:18px;line-height:31px;color:var(--white);text-transform:uppercase}

/* about */
.about-mark{position:absolute;left:118px;top:990px;width:484px;height:425px;display:flex;align-items:center;justify-content:center;gap:18px}
.about-mark .dot{width:60px;height:60px;border-radius:50%;background:var(--yellow)}
.about-mark .name{font-family:"Exo 2",sans-serif;font-weight:600;font-size:38px;color:var(--dark);text-transform:uppercase}
.about-text{position:absolute;left:656px;top:978px;width:410px}
.about-text h3{font-family:"Exo 2",sans-serif;font-weight:600;font-size:25px;color:var(--dark);text-transform:uppercase}
.about-text h2{font-family:"Exo 2",sans-serif;font-weight:600;font-size:31px;color:var(--yellow);text-transform:uppercase;margin-top:8px}
.about-text p{margin-top:30px;font-size:13.4px;line-height:27.5px;color:var(--grey);text-align:justify}
.rule{position:absolute;left:110px;top:1475px;width:980px;height:1px;background:var(--line)}

.section-title{position:absolute;left:0;width:1200px;text-align:center;font-family:"Exo 2",sans-serif;font-weight:700;font-size:36px;color:var(--dark);text-transform:uppercase}
.section-title span{color:var(--yellow)}
.section-desc{position:absolute;left:230px;width:740px;text-align:center;font-size:15.5px;line-height:27px;color:var(--grey)}

/* services */
.services{position:absolute;left:0;top:1655px;width:1200px;height:403px;display:flex}
.service{width:300px;height:403px;padding:30px 0 0 30px;color:var(--white)}
.service.dark{background:var(--dark)}
.service.yellow{background:var(--yellow)}
.service svg{width:64px;height:64px;stroke:var(--white);fill:none;stroke-width:2.2}
.service h4{font-family:"Exo 2",sans-serif;font-weight:600;font-size:18px;line-height:26px;text-transform:uppercase;margin:10px 0 10px;padding-right:10px}
.service ul{list-style:none}
.service li{position:relative;padding-left:21px;padding-right:14px;font-size:13px;line-height:15px;margin-bottom:22px}
.service li::before{content:"";position:absolute;left:2px;top:2px;width:9px;height:5px;border-left:2.5px solid var(--white);border-bottom:2.5px solid var(--white);transform:rotate(-45deg)}

/* celebrate */
.celebrate{position:absolute;left:0;top:2058px;width:1200px;height:587px;background:linear-gradient(100deg,#2e3236 0%,#3d4046 50%,#1d2024 100%)}
.celebrate h2{position:absolute;left:0;top:262px;width:1200px;text-align:center;font-family:"Exo 2",sans-serif;font-weight:700;font-size:47px;line-height:58px;color:var(--white);text-transform:uppercase}

/* team */
.photo{position:absolute;width:312px;height:275px;top:2850px}
.team-card{position:absolute;top:3080px;width:274px;height:193px;background:var(--white);border:1px solid var(--line);text-align:center}
.team-card h5{margin-top:20px;font-family:"Exo 2",sans-serif;font-weight:600;font-size:19px;color:var(--dark);text-transform:uppercase}
.team-card p{margin-top:12px;font-size:13.5px;line-height:22px;color:var(--grey);padding:0 20px}
.socials{display:flex;justify-content:center;gap:10px;margin-top:14px}
.socials span{width:50px;height:50px;border-radius:50%;border:1px solid #cfcfcf}

/* solution */
.solution-photo{position:absolute;left:0;top:3350px;width:568px;height:460px;background:linear-gradient(120deg,#d9d4cc 0%,#8c8a86 55%,#4a4a4c 100%)}
.solution{position:absolute;left:568px;top:3350px;width:632px;height:460px;background:var(--yellow);color:var(--white)}
.solution h2{position:absolute;left:52px;top:56px;font-family:"Exo 2",sans-serif;font-weight:600;font-size:29px;line-height:40px;text-transform:uppercase}
.solution ul{position:absolute;left:52px;top:164px;width:530px;list-style:none}
.solution li{position:relative;padding-left:27px;font-size:13.5px;line-height:25px;margin-bottom:42px}
.solution li::before{content:"";position:absolute;left:2px;top:6px;width:11px;height:6px;border-left:3px solid var(--white);border-bottom:3px solid var(--white);transform:rotate(-45deg)}

/* footer */
.site-footer{position:absolute;left:0;top:3810px;width:1200px;height:394px;background:var(--footer);color:var(--white)}
.site-footer h4{position:absolute;font-family:"Exo 2",sans-serif;font-weight:600;font-size:20px;text-transform:uppercase}
.field{position:absolute;height:36px;background:var(--white);color:var(--ink);font-size:11.5px;padding:13px 12px 0}
.contact-item{position:absolute;left:575px;display:flex;gap:16px;align-items:flex-start}
.contact-item .ico{width:42px;height:42px;border-radius:50%;border:1.5px solid var(--white);display:flex;align-items:center;justify-content:center;flex:none}
.contact-item .ico svg{width:16px;height:16px;fill:var(--white)}
.contact-item b{display:block;font-family:"Exo 2",sans-serif;font-weight:600;font-size:15px;text-transform:uppercase;margin-bottom:4px}
.contact-item span{font-size:12px;line-height:19px}
.footer-brand{position:absolute;left:828px;top:128px;width:240px;text-align:center}
.footer-brand .dot{width:26px;height:26px;background:var(--white);margin:0 auto 14px}
.footer-brand .name{font-family:"Exo 2",sans-serif;font-weight:600;font-size:24px;text-transform:uppercase}
.footer-socials{position:absolute;left:880px;top:254px;display:flex;gap:6px}
.footer-socials span{width:38px;height:38px;border-radius:50%;border:1.5px solid var(--white)}
.copyright{position:absolute;left:0;top:355px;width:1200px;text-align:center;font-size:13px}
</style>
</head>
<body>

<header class="site-header">
  <div class="brand"><span class="brand-dot"></span><span class="brand-name">HR Vantor Consulting</span></div>
  <div class="btn" style="left:907px;top:33px;width:181px;height:53px">Get Started</div>
  <nav class="main-nav">
    <span class="active">Home</span><span>What We Do</span><span>How It Works</span><span>About Us</span><span>Services</span><span>Contact Us</span>
  </nav>
</header>

<section class="hero" role="img" aria-label="Photo of two business colleagues reviewing documents in a dim office">
  <h1>HR Vantor<span>Consulting</span></h1>
  <p>Sed ut perspiciatis unde omnis iste natus<br>error sit voluptatem</p>
</section>

<div class="about-mark"><span class="dot"></span><span class="name">HR Vantor</span></div>
<div class="about-text">
  <h3>About Us</h3>
  <h2>HR Vantor Consulting</h2>
  <p>Sed ut perspiciatis unde omnis iste natus error sit voluptatem accus antium doloremque laudantium, totam rem aperiam, eaque ipsa quae ab illo inventore veritatis et quasi architecto beatae vitae dicta sunt explicabo. Nemo enim ipsam voluptatem quia voluptas sit aspe rnatur aut odit aut fugit, sed quia consequuntur magni dolores eos qui ratione voluptatem sequi nesciunt. Neque porro quisquam est, qui dolorem ipsum quia dolor sit amet, consectetur, adipisci velit, dolore magnam aliquam quaerat voluptatem.</p>
</div>
<div class="btn" style="left:660px;top:1347px;width:154px;height:53px">Read More</div>
<div class="rule"></div>

<h2 class="section-title" style="top:1513px">Our <span>Services</span></h2>
<p class="section-desc" style="top:1568px">We help assess your HR needs and offer ongoing HR Department services or defined projects based on your organization's unique needs and goals</p>

<section class="services">
  <div class="service dark">
    <svg viewBox="0 0 64 64"><circle cx="32" cy="32" r="10"/><path d="M32 6l5 7 8-2 2 8 7 4-3 8 3 8-7 4-2 8-8-2-5 7-5-7-8 2-2-8-7-4 3-8-3-8 7-4 2-8 8 2z"/></svg>
    <h4>Setup</h4>
    <ul><li>Select and implement an HRIS system</li><li>Create Company Handbook</li><li>Write termination procedure</li><li>Set up benefits services</li><li>Set up workers comp vendor</li><li>Create job descriptions for current and anticipated roles</li></ul>
  </div>
  <div class="service yellow">
    <svg viewBox="0 0 64 64"><circle cx="32" cy="10" r="6"/><rect x="22" y="20" width="20" height="10"/><path d="M32 30v8M12 38h40M12 38v6M32 38v6M52 38v6"/><circle cx="12" cy="52" r="7"/><circle cx="32" cy="52" r="7"/><circle cx="52" cy="52" r="7"/></svg>
    <h4>Managing HR Functions/Recruiting</h4>
    <ul><li>Managing HR Functions/Recruiting</li><li>Employee relations</li><li>Investigations</li><li>Leave administration</li><li>Immigration liaison</li><li>Compensation management</li></ul>
  </div>
  <div class="service dark">
    <svg viewBox="0 0 64 64"><path d="M4 14h44M40 8l8 6-8 6M60 32H16M24 26l-8 6 8 6M4 50h40"/><circle cx="52" cy="50" r="8"/><path d="M50 46l5 4-5 4z"/><rect x="4" y="8" width="10" height="12"/></svg>
    <h4>Recurring Procedures</h4>
    <ul><li>Review handbook annually</li><li>Roll out training</li><li>Write offer letters</li><li>Handle employee data and files</li><li>Conduct I-9 audits</li><li>Handle merit and review bonuses</li></ul>
  </div>
  <div class="service yellow">
    <svg viewBox="0 0 64 64"><path d="M4 10h32v20H18l-8 8v-8H4z"/><path d="M26 30v12h20l8 8v-8h6V22H36"/></svg>
    <h4>Partner Communications</h4>
    <ul><li>Manage annual bidding process for benefits review</li><li>Handle workers compensation claims administration</li><li>Manage leave administration between client, employee and vendor(s)</li><li>Handle EDD inquires</li><li>Partner on M&amp;A activity</li></ul>
  </div>
</section>

<section class="celebrate" role="img" aria-label="Photo of a diverse team in conversation at a meeting table">
  <h2>Celebrating 15 Years<br>In Business</h2>
  <div class="btn" style="left:505px;top:392px;width:190px;height:53px">Learn More</div>
</section>

<h2 class="section-title" style="top:2692px">Our <span>Team</span></h2>
<p class="section-desc" style="top:2746px">We help assess your HR needs and offer ongoing HR Department services or defined projects based on your organization's unique needs and goals</p>

<div class="photo" style="left:111px;background:linear-gradient(#6e6e6e,#3a3a3a)" role="img" aria-label="Portrait of a team member"></div>
<div class="photo" style="left:445px;background:linear-gradient(#8a7a6c,#4b4038)" role="img" aria-label="Portrait of a team member"></div>
<div class="photo" style="left:778px;background:linear-gradient(#7a7a7a,#3c3c3c)" role="img" aria-label="Portrait of a team member"></div>

<div class="team-card" style="left:130px"><h5>Jhon Smith</h5><p>Sed ut perspiciatis unde omnis iste natus error sit voluptatem</p><div class="socials"><span></span><span></span></div></div>
<div class="team-card" style="left:463px"><h5>Jhon Smith</h5><p>Sed ut perspiciatis unde omnis iste natus error sit voluptatem</p><div class="socials"><span></span><span></span></div></div>
<div class="team-card" style="left:796px"><h5>Jhon Smith</h5><p>Sed ut perspiciatis unde omnis iste natus error sit voluptatem</p><div class="socials"><span></span><span></span></div></div>

<div class="solution-photo" role="img" aria-label="Photo of two women discussing notes in an HR meeting"></div>
<section class="solution">
  <h2>Your Human Resources<br>Solution</h2>
  <ul>
    <li>HR Vantor Consulting is the solution to all your HR issues. We are a one-stop-shop providing a variety of services</li>
    <li>Whether you have a specific HR need or seek relief by outsourcing altogether, we have you covered</li>
    <li>For some clients, an HR Vantor Consultant is known as the HR de and for others, we simply step in as needed on a project basis</li>
  </ul>
</section>

<footer class="site-footer">
  <h4 style="left:119px;top:60px">Contact Us</h4>
  <div class="field" style="left:119px;top:108px;width:182px">First Name :</div>
  <div class="field" style="left:309px;top:108px;width:182px">Last Name :</div>
  <div class="field" style="left:119px;top:152px;width:182px">Company Name :</div>
  <div class="field" style="left:309px;top:152px;width:182px">Email address :</div>
  <div class="field" style="left:119px;top:198px;width:372px">Comment :</div>
  <div class="btn" style="left:119px;top:248px;width:116px;height:42px;font-size:14px">Submit</div>

  <h4 style="left:584px;top:60px">Address</h4>
  <div class="contact-item" style="top:100px"><div class="ico"><svg viewBox="0 0 16 16"><path d="M8 1a5 5 0 015 5c0 4-5 9-5 9S3 10 3 6a5 5 0 015-5zm0 3a2 2 0 100 4 2 2 0 000-4z"/></svg></div><div><b>Address</b><span>#25 Lorem Ipsum Dummy<br>Lorem Ipsum Dummy</span></div></div>
  <div class="contact-item" style="top:180px"><div class="ico"><svg viewBox="0 0 16 16"><path d="M4 1l3 3-2 2c1 2 3 4 5 5l2-2 3 3-2 3C7 15 1 9 1 3z"/></svg></div><div><b>Phone</b><span>00.121.1231</span></div></div>
  <div class="contact-item" style="top:255px"><div class="ico"><svg viewBox="0 0 16 16"><path d="M1 3h14v2L8 9 1 5zm0 4l7 4 7-4v6H1z"/></svg></div><div><b>Email</b><span>info@hrvantorconsulting.com</span></div></div>

  <div class="footer-brand"><div class="dot"></div><div class="name">HR Vantor<br>Consulting</div></div>
  <div class="footer-socials"><span></span><span></span><span></span></div>

  <p class="copyright">©2021 HR Vantor .All rights reserved.</p>
</footer>

</body>
</html>
```